IT Company needs full suite of stationery

Our company 4627 Vantor Holdings Inc. is an IT company based in Toronto, Canada. Based on our logo we would like to see business cards(front and back), letterhead, envelope, brochure template. Design would be simple, not too bright, modern but can be used for many years, good theme throughout. Our official logo is the the fullcolor_a, full company name is 4627 Vantor Holdings Inc., Please include full company name on all pieces. Logo can be modified to be the graphic only with the "4627 Holdings", I have cropped it myself for a couple files but I am no designer. We will provide lots of feedback so post early and often.

Project Deadline Extended
Reason: Very busy around the holidays, like a lot of the designs currently submitted, will definitely be picking one. Thanks for your submissions and merry Christmas and Happy New Year to everyone.

Industry/Entity Type

Business

```html
<!DOCTYPE html>
<html lang="en">
<head>
<meta charset="utf-8">
<title>4627 Vantor Holdings Inc. — Stationery Suite</title>
<link rel="stylesheet" href="https://fonts.googleapis.com/css2?family=Roboto:wght@300;400;500;700&display=swap">
<style>
  :root {
    --green: #4a9c3c;
    --green-faint: #e3eee0;
    --ink: #2f3133;
    --text: #55585b;
    --muted: #8a8d90;
    --paper: #ffffff;
    --stage: #dcdddf;
    --edge: #c9cacc;
  }
  * { box-sizing: border-box; margin: 0; padding: 0; }
  html, body { width: 1200px; height: 790px; overflow: hidden; }
  body {
    background: var(--stage);
    font-family: "Roboto", Arial, sans-serif;
    color: var(--text);
    position: relative;
  }
  .sheet {
    position: absolute;
    background: var(--paper);
    border: 1px solid var(--edge);
    overflow: hidden;
  }

  /* brand lockup */
  .brand { display: flex; align-items: center; gap: 8px; }
  .brand-dot { width: 22px; height: 22px; border-radius: 50%; background: var(--green); flex: none; }
  .brand-name { font-weight: 700; color: var(--green); font-size: 20px; letter-spacing: 0.5px; white-space: nowrap; }

  .icon { width: 9px; height: 9px; flex: none; fill: none; stroke: var(--ink); stroke-width: 1.6; }
  .contact-row { display: flex; gap: 6px; align-items: flex-start; font-size: 6.5px; line-height: 1.45; color: var(--text); }
  .website { font-weight: 500; color: var(--ink); letter-spacing: 4px; font-size: 10px; }

  /* letterhead */
  .letterhead { left: 50px; top: 110px; width: 460px; height: 650px; }
  .letterhead .brand { position: absolute; left: 38px; top: 100px; }
  .letterhead .brand-dot { width: 34px; height: 34px; }
  .letterhead .brand-name { font-size: 26px; }
  .letterhead .contact { position: absolute; right: 30px; top: 28px; display: grid; gap: 8px; width: 110px; }
  .letter { position: absolute; left: 92px; top: 180px; width: 300px; font-size: 6.5px; line-height: 1.6; }
  .letter p { margin-bottom: 10px; }
  .letter .salute { font-weight: 700; color: var(--ink); margin-bottom: 2px; }
  .signature { width: 52px; height: 22px; background: linear-gradient(90deg, #e9eaeb, #f4f4f5); margin: 4px 0; }
  .signer { font-weight: 700; color: var(--ink); }
  .letterhead .watermark {
    position: absolute; right: -90px; bottom: 90px; width: 260px; height: 260px;
    border-radius: 50%; border: 14px solid var(--green-faint); background: #f3f7f2;
  }
  .letterhead .website { position: absolute; right: 30px; bottom: 30px; }

  /* envelope */
  .envelope { left: 560px; top: 70px; width: 600px; height: 300px; }
  .envelope .brand { position: absolute; right: 40px; top: 40px; }
  .envelope .brand-dot { width: 34px; height: 34px; }
  .envelope .brand-name { font-size: 26px; }
  .envelope .website { position: absolute; left: 40px; bottom: 36px; }

  /* business cards */
  .card { width: 290px; height: 166px; top: 440px; }
  .card-front { left: 560px; }
  .card-back { left: 880px; }
  .card-front .brand { position: absolute; left: 20px; top: 20px; }
  .card-front .person { position: absolute; left: 120px; top: 62px; display: flex; gap: 6px; align-items: flex-start; }
  .person-name { font-size: 10px; font-weight: 700; color: var(--ink); }
  .person-role { font-size: 7px; color: var(--muted); }
  .card-front .details { position: absolute; left: 20px; bottom: 18px; display: grid; gap: 6px; }
  .card-back .website { position: absolute; right: 18px; bottom: 18px; font-size: 7px; letter-spacing: 2px; }
</style>
</head>
<body>

<svg width="0" height="0" style="position:absolute">
  <symbol id="pin" viewBox="0 0 10 10"><path d="M5 9.5 C2 6 1.5 4.8 1.5 3.8 A3.5 3.5 0 0 1 8.5 3.8 C8.5 4.8 8 6 5 9.5 Z"/><circle cx="5" cy="3.8" r="1.2"/></symbol>
  <symbol id="globe" viewBox="0 0 10 10"><circle cx="5" cy="5" r="4"/><path d="M1 5 H9 M5 1 C3 3.5 3 6.5 5 9 M5 1 C7 3.5 7 6.5 5 9"/></symbol>
  <symbol id="phone" viewBox="0 0 10 10"><rect x="2.5" y="1" width="5" height="8" rx="1"/><path d="M4.3 7.5 H5.7"/></symbol>
  <symbol id="person" viewBox="0 0 10 10"><circle cx="5" cy="3.3" r="2"/><path d="M1.5 9.2 C1.8 6.8 3.2 6 5 6 C6.8 6 8.2 6.8 8.5 9.2"/></symbol>
</svg>

<section class="sheet letterhead" aria-label="Letterhead">
  <div class="contact">
    <div class="contact-row"><svg class="icon"><use href="#pin"/></svg><span>4627 Vantor Holdings Inc.<br>12 Harbour Road, Toronto, ON Canada</span></div>
    <div class="contact-row"><svg class="icon"><use href="#phone"/></svg><span>+1 416 555 0142</span></div>
    <div class="contact-row"><svg class="icon"><use href="#globe"/></svg><span>info@4627holdings.ca</span></div>
  </div>
  <div class="brand"><span class="brand-dot"></span><span class="brand-name">4627 Holdings</span></div>
  <div class="watermark" aria-hidden="true"></div>
  <article class="letter">
    <p>July 2, 2012</p>
    <p class="salute">Dear Sir,</p>
    <p>12 Harbour Road, Toronto</p>
    <p>Lorem Ipsum is simply dummy text of the printing and typesetting industry. Lorem Ipsum has been the industry's standard dummy text ever since the 1500s, when an unknown printer took a galley of type and scrambled it to make a type specimen book.</p>
    <p>Lorem Ipsum is simply dummy text of the printing and typesetting industry. Lorem Ipsum has been the industry's standard dummy text ever since the 1500s, when an unknown printer took a galley of type and scrambled it to make a type specimen book.</p>
    <p>Lorem Ipsum is simply dummy text of the printing and typesetting industry. Lorem Ipsum has been the industry's standard dummy text ever since the 1500s, when an unknown printer took a galley of type and scrambled it to make a type specimen book.</p>
    <p style="margin-bottom:2px">Best Regards,</p>
    <div class="signature" role="img" aria-label="Handwritten signature"></div>
    <div class="signer">Daniel Reyes</div>
    <div>Director</div>
    <div>12 Harbour Road, Toronto</div>
  </article>
  <div class="website">www.4627holdings.ca</div>
</section>

<section class="sheet envelope" aria-label="Envelope">
  <div class="brand"><span class="brand-dot"></span><span class="brand-name">4627 Holdings</span></div>
  <div class="website">www.4627holdings.ca</div>
</section>

<section class="sheet card card-front" aria-label="Business card front">
  <div class="brand"><span class="brand-dot" style="width:16px;height:16px"></span><span class="brand-name" style="font-size:13px">4627 Holdings</span></div>
  <div class="person">
    <svg class="icon" style="width:11px;height:11px"><use href="#person"/></svg>
    <div><div class="person-name">Daniel Reyes</div><div class="person-role">Director</div></div>
  </div>
  <div class="details">
    <div class="contact-row"><svg class="icon"><use href="#pin"/></svg><span>4627 Vantor Holdings Inc.<br>12 Harbour Road, Toronto, ON Canada</span></div>
    <div class="contact-row"><svg class="icon"><use href="#globe"/></svg><span>+1 416 555 0142<br>www.4627holdings.ca</span></div>
  </div>
</section>

<section class="sheet card card-back" aria-label="Business card back">
  <div class="website">www.4627holdings.ca</div>
</section>

</body>
</html>
```